Stationary Package for New Bookkeeping Business

We need the following stationary designs:

- Business Card
- Letterhead
- With Comps
- Envelopes
- Paper Folder
- Email Signature

We will provide accounting and bookkeeping services to small business. We would like have the main color as blue and have a modern professional look.

Variations of colour and shades of blue welcome
Preference for deeper darker blue - navy

Variations of font in logo also welcome

Industry/Entity Type

Accounting

Requirements
Must have
• Danielle
B.Bus (Accounting)
Registered BAS Agent

Phone 0491 286 537
Post PO Box 947 Wrenfield NSW 2689

Email danielle@corvalbookkeeping.com

Business Card to be bold and eye catching

Should not have
• Letter head to not have too much colour on it

```html
<!DOCTYPE html>
<html lang="en">
<head>
<meta charset="utf-8">
<title>Corval Bookkeeping – Business Card</title>
<link href="https://fonts.googleapis.com/css2?family=Questrial&family=Roboto+Condensed:wght@400;700&display=swap" rel="stylesheet">
<style>
  :root {
    --navy: #0b5894;
    --navy-deep: #084a7e;
    --slate: #6f7383;
    --paper: #fbfbfa;
    --backdrop: #e6e8ec;
  }
  * { margin: 0; padding: 0; box-sizing: border-box; }
  html, body { width: 1200px; height: 800px; overflow: hidden; }
  body {
    background: var(--backdrop);
    font-family: "Questrial", "Century Gothic", sans-serif;
    position: relative;
  }
  .card {
    position: absolute;
    top: 251px;
    width: 520px;
    height: 297px;
    box-shadow: 0 6px 18px rgba(0,0,0,0.12);
  }
  .card--front { left: 60px; background: var(--paper); }
  .card--back {
    left: 620px;
    background: var(--navy);
    display: flex;
    align-items: center;
    justify-content: center;
  }
  .brand {
    display: flex;
    align-items: center;
    gap: 12px;
  }
  .brand__square {
    width: 44px;
    height: 44px;
    background: var(--slate);
    flex: none;
  }
  .brand__name {
    font-family: "Questrial", sans-serif;
    font-size: 27px;
    line-height: 1.0;
    color: var(--navy);
  }
  .card--front .brand { position: absolute; left: 44px; top: 46px; }
  .card--back .brand__name { color: #ffffff; font-size: 32px; }
  .card--back .brand__square { width: 52px; height: 52px; background: #8a8e9c; }

  .holder {
    position: absolute;
    right: 40px;
    top: 150px;
    text-align: right;
  }
  .holder__name {
    font-family: "Roboto Condensed", sans-serif;
    font-weight: 700;
    font-size: 18px;
    letter-spacing: 0.3px;
    color: var(--slate);
  }
  .holder__role {
    font-family: "Questrial", sans-serif;
    font-size: 13px;
    color: var(--slate);
    margin-top: 2px;
  }
  .rule {
    position: absolute;
    height: 7px;
  }
  .rule--slate { background: var(--slate); right: 40px; top: 200px; width: 122px; }
  .rule--navy { background: var(--navy); left: 44px; bottom: 42px; width: 294px; }

  .contact {
    position: absolute;
    left: 44px;
    top: 196px;
    font-size: 11.5px;
    line-height: 1.55;
    color: var(--slate);
  }
  .contact__label { color: var(--navy); font-weight: 700; font-family: "Roboto Condensed", sans-serif; }
</style>
</head>
<body>
  <section class="card card--front" aria-label="Business card front">
    <div class="brand">
      <span class="brand__square"></span>
      <span class="brand__name">Corval<br>Bookkeeping</span>
    </div>

    <div class="holder">
      <p class="holder__name">DANIELLE B.BUS</p>
      <p class="holder__role">Accounting</p>
    </div>
    <div class="rule rule--slate"></div>

    <div class="contact">
      <p><span class="contact__label">T:</span> 0491 286 537</p>
      <p><span class="contact__label">E:</span> danielle@corvalbookkeeping.com</p>
      <p>Post PO Box 947 Wrenfield NSW 2689</p>
    </div>
    <div class="rule rule--navy"></div>
  </section>

  <section class="card card--back" aria-label="Business card back">
    <div class="brand">
      <span class="brand__square"></span>
      <span class="brand__name">Corval<br>Bookkeeping</span>
    </div>
  </section>
</body>
</html>
```